Coastal Learner Bureau business cards

Australian company about to start offering its services. We recruit international students to come to study English, vocational education and postgraduate courses in Australia. We help them find the institution and select the right city they want to come to Australia. We are a young, online oriented and supportive agency. Our clients are between 18 and 35 years old, mainly University students, young professionals or people with work experience. We provide much more information that any other agency offer. We administrate a Facebook group with more than 11.000 members that daily ask questions about general information when coming to Australia, while they are here and even after they leave the country

Target Market(s)

International students from South America, Central America and Europe

Industry/Entity Type

Student

Contact Information for Business Card

Tomas Bilbrea
Managing Director
tomas@kelvarin.com.au
www.kelvoria.com.au
+61 491058264
Melbourne, Australia

Font styles to use
Serif
Sans Serif

Colors

Designer to choose colors to be used in the design.

Requirements
Must have
• Horizontal design
• Standard business card size and shape. If font uses green or yellow colours, they will have to match the ones from the logo
Nice to have
• UPDATE: Use the contents of the green image to design one of the card sides. Use our logo in the background of that side as watermark.
• Passport image, or immigration stamps. A picture of the Yarra River (from Melbourne) would be cool as well.
Should not have
• Non-standard business card size and shape
• Not black as the background colour of any sides as we are not a VIP agency or a hight class service. We are orientes to young people and they like colours, pictures, something attractive.
• Vertical design
• NO YELLOW or BLACK AS THE BACKGROUND COLOUR OF ANY SIDE OF THE BIZ CARD

```html
<!DOCTYPE html>
<html lang="en">
<head>
<meta charset="utf-8">
<title>Coastal Learner Bureau business cards</title>
<link href="https://fonts.googleapis.com/css2?family=Arimo:wght@400;700&display=swap" rel="stylesheet">
<style>
  :root {
    --bg: #d9dcdb;
    --card-white: #ffffff;
    --card-shade: #eef0ef;
    --green: #0f5a3c;
    --green-dark: #0b4a31;
    --gold: #d9a816;
    --gold-dark: #b88c0c;
    --ink: #1d1d1b;
    --soft-white: #e9f1ec;
  }
  * { box-sizing: border-box; margin: 0; padding: 0; }
  html, body { width: 1200px; height: 997px; overflow: hidden; }
  body {
    background: var(--bg);
    font-family: "Arimo", Arial, sans-serif;
    position: relative;
  }
  .card {
    position: absolute;
    left: 290px;
    width: 620px;
    height: 354px;
    border-radius: 22px;
    overflow: hidden;
    background: linear-gradient(180deg, var(--card-white), var(--card-shade));
    box-shadow: 0 10px 30px rgba(0,0,0,0.18);
  }
  .card--front { top: 118px; }
  .card--back { top: 526px; }

  .brand {
    position: absolute;
    display: flex;
    align-items: center;
    gap: 12px;
    color: var(--green);
    font-weight: 700;
    letter-spacing: 0.5px;
  }
  .brand__dot {
    border-radius: 50%;
    background: var(--gold);
  }
  .card--front .brand { left: 0; right: 0; top: 118px; justify-content: center; font-size: 54px; }
  .card--front .brand__dot { width: 30px; height: 30px; }
  .tagline {
    position: absolute;
    right: 150px;
    bottom: 58px;
    color: var(--green);
    font-weight: 700;
    font-size: 17px;
    letter-spacing: 1.5px;
  }

  .card--back .brand { left: 0; right: 0; top: 42px; justify-content: center; font-size: 46px; }
  .card--back .brand__dot { width: 24px; height: 24px; }
  .bands { position: absolute; inset: 0; }
  .holder {
    position: absolute;
    left: 0; right: 0;
    top: 156px;
    text-align: center;
  }
  .holder__name { color: var(--green-dark); font-weight: 700; font-size: 19px; letter-spacing: 0.5px; }
  .holder__role { color: var(--ink); font-size: 15px; margin-top: 2px; }

  .contacts {
    position: absolute;
    left: 28px;
    bottom: 22px;
    list-style: none;
    color: var(--soft-white);
    font-size: 16px;
  }
  .contacts li { display: flex; align-items: center; gap: 12px; height: 28px; }
  .contacts .icon {
    width: 20px; height: 20px;
    border-radius: 50%;
    background: var(--gold);
    display: flex; align-items: center; justify-content: center;
    flex: none;
  }
  .website {
    position: absolute;
    right: 28px;
    top: 224px;
    color: var(--gold);
    font-weight: 700;
    font-size: 18px;
    letter-spacing: 0.5px;
  }
</style>
</head>
<body>

<section class="card card--front" aria-label="Card front">
  <div class="brand"><span class="brand__dot"></span>Kelvoria</div>
  <p class="tagline">Hacemos más por ti!</p>
</section>

<section class="card card--back" aria-label="Card back">
  <div class="brand"><span class="brand__dot"></span>Kelvoria</div>
  <svg class="bands" viewBox="0 0 620 354" width="620" height="354" aria-hidden="true">
    <polygon points="0,196 172,196 208,148 430,148 464,196 620,196 620,354 0,354" fill="var(--gold)"/>
    <polygon points="172,196 208,148 222,148 190,196" fill="var(--gold-dark)" opacity="0.5"/>
    <polygon points="0,206 440,206 470,176 620,176 620,354 0,354" fill="var(--green)"/>
  </svg>
  <div class="holder">
    <p class="holder__name">TOMAS BILBREA</p>
    <p class="holder__role">Managing Director</p>
  </div>
  <p class="website">www.kelvoria.com.au</p>
  <ul class="contacts">
    <li><span class="icon"></span>kelvoria</li>
    <li>
      <span class="icon">
        <svg width="12" height="12" viewBox="0 0 24 24" aria-hidden="true"><path d="M6.6 10.8a15 15 0 0 0 6.6 6.6l2.2-2.2a1 1 0 0 1 1-.25 11.4 11.4 0 0 0 3.6.57 1 1 0 0 1 1 1V20a1 1 0 0 1-1 1A17 17 0 0 1 3 4a1 1 0 0 1 1-1h3.5a1 1 0 0 1 1 1c0 1.25.2 2.45.57 3.6a1 1 0 0 1-.25 1z" fill="var(--green)"/></svg>
      </span>+61 491058264
    </li>
    <li>
      <span class="icon">
        <svg width="12" height="12" viewBox="0 0 24 24" aria-hidden="true"><rect x="2" y="5" width="20" height="14" rx="2" fill="var(--green)"/><path d="M3 6l9 7 9-7" stroke="var(--gold)" stroke-width="2" fill="none"/></svg>
      </span>tomas@kelvarin.com.au
    </li>
  </ul>
</section>

</body>
</html>
```